Animal Eye Clinic needs a Business card

We are a new veterinary ophthalmology practice (Ridgeline Pet Vision Care) and we need a business card designed. We only see animal eyes - we are not a regular veterinary clinic. We already have a logo. We are looking for a professional, good looking business card to hand out to our clients. We are looking for something simple but professional and contemporary. Our logo is likely the only picture/graphic that needs to be on the card.
Updates

Contact Information for Business Card

Delia Vossman, BSc, DVM, MSc, DipACVO
Veterinary Ophthalmologist

Phone: 250.418.3927
Email: ridgelinepetvisioncare@mailbox-example.net
Website: ridgelinepetvisioncare-example.net
Address: 1874 Thornbury Rd
Kelowna, BC, V1X 4M9

Colors

Designer to choose colors to be used in the design.

Requirements
Must have
• Our logo (attached)

```html
<!DOCTYPE html>
<html lang="en">
<head>
<meta charset="utf-8">
<title>Ridgeline Pet Vision Care – Business Card</title>
<link href="https://fonts.googleapis.com/css2?family=Roboto:wght@400;500&display=swap" rel="stylesheet">
<style>
  :root {
    --backdrop: #1b1b1b;
    --card: #262626;
    --card-edge: #303030;
    --teal: #1697a6;
    --silver: #c9c9c9;
    --ink: #f2f2f2;
    --rule: #e8e8e8;
  }
  * { margin: 0; padding: 0; box-sizing: border-box; }
  html, body {
    width: 1200px; height: 900px; overflow: hidden;
    background: var(--backdrop);
    font-family: "Roboto", sans-serif;
  }
  .sheet {
    position: relative; width: 1200px; height: 900px;
    display: flex; flex-direction: column; align-items: center;
    justify-content: center; gap: 40px;
  }
  .card {
    position: relative; width: 700px; height: 400px;
    background: linear-gradient(135deg, var(--card-edge), var(--card));
    box-shadow: 0 12px 30px rgba(0,0,0,.55);
  }
  /* front */
  .card--front { display: flex; align-items: center; justify-content: center; gap: 18px; }
  .brand-dot { width: 34px; height: 34px; border-radius: 50%; background: var(--silver); }
  .brand-name--front { font-size: 30px; font-weight: 500; color: var(--silver); letter-spacing: .5px; }
  /* back */
  .card--back .brand {
    position: absolute; top: 48px; right: 44px;
    display: flex; align-items: center; gap: 12px;
  }
  .brand-dot--teal { width: 26px; height: 26px; background: var(--teal); }
  .brand-name--back { font-size: 24px; font-weight: 500; color: var(--teal); }
  .person { position: absolute; left: 50px; top: 118px; }
  .person__name { font-size: 40px; font-weight: 500; color: var(--teal); line-height: 1.1; }
  .person__creds, .person__title { font-size: 17px; color: var(--ink); line-height: 1.45; }
  .address { position: absolute; left: 50px; top: 236px; font-size: 18px; color: var(--ink); }
  .rule { position: absolute; left: 50px; right: 44px; top: 276px; height: 2px; background: var(--rule); }
  .contact { position: absolute; left: 50px; top: 292px; font-size: 18px; color: var(--ink); line-height: 1.55; }
  .contact .label { color: var(--teal); }
  .contact .strong { font-weight: 500; }
</style>
</head>
<body>
<main class="sheet">
  <section class="card card--front">
    <span class="brand-dot"></span>
    <span class="brand-name brand-name--front">Ridgeline Pet Vision Care</span>
  </section>

  <section class="card card--back">
    <div class="brand">
      <span class="brand-dot brand-dot--teal"></span>
      <span class="brand-name brand-name--back">Ridgeline Pet Vision Care</span>
    </div>
    <div class="person">
      <h1 class="person__name">Delia Vossman</h1>
      <p class="person__creds">BSc, DVM, MSc, DipACVO</p>
      <p class="person__title">Veterinary Ophthalmologist</p>
    </div>
    <p class="address">Address: 1874 Thornbury Rd Kelowna, BC, V1X 4M9</p>
    <div class="rule"></div>
    <div class="contact">
      <p><span class="label">P:</span> 250.418.3927 <span class="label">| E:</span> ridgelinepetvisioncare@mailbox-example.net</p>
      <p><span class="label">W:</span> www.<span class="strong">ridgelinepetvisioncare-example</span>.net</p>
    </div>
  </section>
</main>
</body>
</html>
```